SnackOrbit!!! A Vending Machine Business Looking for an attractive website.

We are a vending machine business in Northern Michigan. We have changed our name and have rebranded our company. We would like an attractive website that shares who we are, what services we provide, the products we offer in our machines, along with a form businesses can fill out to see if they are a good fit for our company. I would like to have a Home Page, About SnackOrbit, Why Choose SnackOrbit?, Products & Services, Contact Us (With a Login Option), and a page with a questionnaire for thos interested in getting a FREE Vending Machine.

Target Market(s)

Businesses, Campgrounds, Schools, and many more in Northern Michigan

Industry/Entity Type

Vending Machines

Coding

Coded - Design and coding required

Number of Pages Required

5+ page

Requirements
Must have
• An inviting and enticing Home Page. I want to get my potential clients engaged in our website.
Nice to have
• Possibly background photos from Northern Michigan
Should not have
• A corporate feel. I do not want a boring website.

```html
<!DOCTYPE html>
<html lang="en">
<head>
<meta charset="utf-8">
<title>SnackOrbit – Crave. Vend. Repeat.</title>
<link rel="stylesheet" href="https://fonts.googleapis.com/css2?family=Lexend:wght@400;500;600;700;800&family=Poppins:wght@400;500;600&display=swap">
<style>
:root{
  --navy:#262250;
  --navy-deep:#1f1b45;
  --green:#2b5a24;
  --green-bar:#3a5a22;
  --ink:#1b1b1b;
  --muted:#444;
  --white:#fff;
  --ring:#e6e6ea;
  --star:#f47a2a;
}
*{box-sizing:border-box;margin:0;padding:0}
html,body{width:1200px;height:3044px;overflow:hidden}
body{font-family:"Poppins",sans-serif;color:var(--ink);background:#fff;position:relative}
h1,h2,h3,.brand{font-family:"Lexend",sans-serif}
.abs{position:absolute}

.topbar{height:33px;background:var(--navy);color:#fff;font-size:13px;display:flex;align-items:center;justify-content:center}
.topbar b{font-weight:600;margin-left:4px}

.nav{height:85px;position:relative;background:#fff}
.nav .brand{position:absolute;left:106px;top:22px;font-size:36px;font-weight:700;color:var(--navy);display:flex;align-items:center;gap:8px}
.nav .brand i{display:block;width:30px;height:30px;background:var(--green);border-radius:50%}
.menu{position:absolute;left:393px;top:32px;display:flex;gap:32px;font-size:13.5px;color:var(--navy)}
.btn-pill{position:absolute;top:25px;height:35px;border-radius:18px;color:#fff;font-size:13.5px;display:flex;align-items:center;justify-content:center}
.btn-contact{left:912px;width:106px;background:var(--green)}
.btn-login{left:1023px;width:71px;background:var(--navy)}

.hero{position:relative;height:543px;background:radial-gradient(ellipse at 72% 45%,#6d6638 0%,#3a3424 30%,#1c1a18 60%,#0f0e0e 100%)}
.hero-text{position:absolute;left:106px;top:172px;color:#fff}
.hero h1{font-size:42px;font-weight:800;line-height:48px;letter-spacing:-0.5px}
.hero p{font-size:18px;font-weight:500;margin-top:26px}
.hero .cta{margin-top:22px;width:141px;height:43px;border-radius:22px;background:var(--green);display:flex;align-items:center;justify-content:center;gap:6px;font-size:15px;font-weight:500}

.about{height:344px;background:var(--navy);color:#fff;text-align:center;padding-top:71px}
.about h2{font-size:31px;font-weight:500}
.about p{width:740px;margin:14px auto 0;font-size:13.5px;line-height:22px}
.outline-btn{display:inline-block;margin-top:28px;border:1px solid #fff;border-radius:3px;padding:7px 16px;font-size:13.5px}

.why{position:relative;height:634px}
.why h2{position:absolute;top:76px;width:100%;text-align:center;font-size:31px;font-weight:500}
.ring{position:absolute;left:396px;top:116px;width:408px;height:380px;border:1px solid var(--ring);border-radius:50%}
.ring.inner{left:446px;top:166px;width:308px;height:280px}
.machine{position:absolute;left:523px;top:164px;width:156px;height:289px;background:linear-gradient(90deg,#9ea1a5,#d6d8da 40%,#8f9296);border-radius:4px}
.icon{position:absolute;width:76px;height:76px;border-radius:50%;background:var(--navy);border:4px solid #fff;box-shadow:0 0 0 1px var(--navy);display:flex;align-items:center;justify-content:center}
.feat{position:absolute;width:282px;font-size:12.5px;line-height:20.4px;color:var(--muted)}
.feat h3{font-size:15.5px;font-weight:500;color:var(--ink);margin-bottom:4px}
.feat.left{text-align:right;left:142px}
.feat.right{left:775px;width:290px}
.feat b{color:var(--ink);font-weight:600}
.faint-brand{position:absolute;left:779px;top:500px;font-size:40px;font-weight:700;color:#d9d9de}

.cta-band{position:relative;height:526px;background:linear-gradient(180deg,#8b98a1 0%,#74828c 55%,#5f5a56 100%)}
.cta-photo{position:absolute;left:0;top:0;width:579px;height:526px;background:linear-gradient(90deg,#3a3a3c 0%,#55585d 40%,#c6412b 70%,#7e8890 100%)}
.cta-copy{position:absolute;left:677px;top:154px;width:380px;color:#fff}
.cta-copy h2{font-size:31px;font-weight:500;line-height:39px}
.cta-copy p{font-size:13.5px;line-height:22px;margin-top:14px}
.cta-copy .solid{display:inline-block;margin-top:24px;background:var(--navy);padding:8px 16px;border-radius:3px;font-size:13.5px}

.testi{position:relative;height:498px}
.testi h2{position:absolute;top:76px;width:100%;text-align:center;font-size:31px;font-weight:500}
.card{position:absolute;width:282px;height:228px;border:1px solid #e2e2e2;border-radius:8px;background:#fff;overflow:hidden}
.card p{padding:12px 15px 0;font-size:13.5px;line-height:21.6px;color:#333}
.card-foot{position:absolute;left:0;bottom:0;width:100%;height:59px;background:var(--navy);color:#fff}
.avatar{position:absolute;left:14px;bottom:8px;width:66px;height:66px;border-radius:50%;background:#c8c4c0;border:3px solid #fff}
.card-foot .who{position:absolute;left:90px;top:10px;font-family:"Lexend",sans-serif;font-size:14px;font-weight:500}
.card-foot .who span{display:block;font-family:"Poppins",sans-serif;font-size:11.5px;font-weight:400}
.stars{position:absolute;right:12px;top:18px;color:var(--star);font-size:12px;letter-spacing:1px}
.arrow{position:absolute;top:258px;width:36px;height:36px;border-radius:50%;background:#fff;box-shadow:0 2px 8px rgba(0,0,0,.15);display:flex;align-items:center;justify-content:center}

.footer{position:relative;height:339px;background:var(--navy);color:#fff}
.footer .brand{position:absolute;top:55px;width:100%;text-align:center;font-size:46px;font-weight:700}
.rule{position:absolute;left:142px;width:917px;height:1px;background:rgba(255,255,255,.25)}
.foot-links{position:absolute;left:142px;top:186px;width:917px;display:flex;justify-content:space-around;font-size:13.5px}
.foot-links .on{font-weight:600}
.contact-row{position:absolute;left:142px;top:254px;width:917px;display:flex;justify-content:space-between}
.c-item{display:flex;align-items:center;gap:14px;width:290px;font-size:13.5px;line-height:18px}
.c-item+.c-item{border-left:1px solid rgba(255,255,255,.25);padding-left:30px}
.c-icon{width:40px;height:40px;border-radius:50%;background:rgba(255,255,255,.16);display:flex;align-items:center;justify-content:center;flex:none}
.c-item small{display:block;font-size:11.5px;font-weight:600}
.bottom{height:42px;background:var(--green-bar);color:#fff;font-size:13px;position:relative}
.bottom span{position:absolute;left:142px;top:12px}
.socials{position:absolute;right:142px;top:8px;display:flex;gap:6px}
.socials i{display:block;width:28px;height:28px;border:1.5px solid #fff;border-radius:50%}
</style>
</head>
<body>

<div class="topbar">Lorem Ipsum is simply dummy text of the printing and typesetting industry. - <b>Click Here</b></div>

<header class="nav">
  <div class="brand"><i></i>SnackOrbit</div>
  <nav class="menu"><span>Home</span><span>About SnackOrbit</span><span>Why Choose Us?</span><span>Products &amp; Services</span></nav>
  <div class="btn-pill btn-contact">Contact Us</div>
  <div class="btn-pill btn-login">Login</div>
</header>

<section class="hero" role="img" aria-label="Photo of lit vending machines stocked with drinks at night">
  <div class="hero-text">
    <h1>SnackOrbit: Crave.<br>Vend. Repeat.</h1>
    <p>Elevating Snacking, One Vend at a Time</p>
    <div class="cta">Contact Us
      <svg width="13" height="12" viewBox="0 0 13 12"><path d="M1 6h10M7 2l4 4-4 4" stroke="#fff" stroke-width="2" fill="none"/></svg>
    </div>
  </div>
</section>

<section class="about">
  <h2>About SnackOrbit</h2>
  <p>Welcome to SnackOrbit, where snacking meets delight! We're not just about vending machines;we're your culinary companions, your flavor curators, and your secret stash of happiness. Marcus and Elena, the dynamic duo behind SnackOrbit, have a passion for all things tasty. With backgrounds in sales and a penchant for personal connections, they've transformed the vending experience into an art form.</p>
  <span class="outline-btn">Read More</span>
</section>

<section class="why">
  <h2>Why Choose SnackOrbit?</h2>
  <div class="ring"></div><div class="ring inner"></div>
  <div class="machine" role="img" aria-label="Photo of a snack vending machine"></div>

  <div class="icon" style="left:437px;top:134px"><svg width="34" height="34" viewBox="0 0 34 34"><path d="M17 28 6 16a6 6 0 0 1 11-7 6 6 0 0 1 11 7z" stroke="#fff" stroke-width="2" fill="none"/></svg></div>
  <div class="icon" style="left:686px;top:134px"><svg width="34" height="34" viewBox="0 0 34 34"><path d="M17 4l4 9 9 1-7 6 2 9-8-5-8 5 2-9-7-6 9-1z" stroke="#fff" stroke-width="2" fill="none"/></svg></div>
  <div class="icon" style="left:437px;top:378px"><svg width="34" height="34" viewBox="0 0 34 34"><circle cx="17" cy="17" r="12" stroke="#fff" stroke-width="2" fill="none"/><path d="M11 20q6 6 12 0" stroke="#fff" stroke-width="2" fill="none"/><circle cx="13" cy="14" r="1.5" fill="#fff"/><circle cx="21" cy="14" r="1.5" fill="#fff"/></svg></div>
  <div class="icon" style="left:686px;top:378px"><svg width="34" height="34" viewBox="0 0 34 34"><path d="M5 29h24M9 29V19M15 29V14M21 29V17M27 29V9M7 15l7-6 6 4 8-8" stroke="#fff" stroke-width="2" fill="none"/></svg></div>

  <div class="feat left" style="top:142px"><h3>1. Local Love</h3>We celebrate the heart of Michigan by partnering with local legends. Say hello to <b>Birch Hollow Jerky and Pine Shore Potato Chips</b>—our hometown heroes. Their flavors dance on your taste buds, and we're thrilled to bring them straight to your workplace.</div>
  <div class="feat left" style="top:385px"><h3>2. Unleash Your Cravings</h3>SnackOrbit isn't bound by corporate ties. We're the rebels of the vending world. Craving a bag of crispy, kettle-cooked chips? Done. Hankering for jerky that packs a punch? We've got you covered. Our machines are like treasure chests, waiting for you to unlock flavor magic.</div>
  <div class="feat right" style="top:142px"><h3>3. Quality Meets Convenience</h3>Imagine this: You're mid-meeting, and your stomach growls. Fear not! SnackOrbit's machines offer top-notch snacks and beverages. It's like having a mini food festival at your fingertips.<br><b>Tap to Pay</b> : No fumbling for change! SnackOrbit accepts tap-to-pay options, credit cards, and even mobile wallet apps. Seamless snacking, guaranteed.</div>
  <div class="feat right" style="top:385px;width:300px"><h3>4. Pandemic-Proof &amp; Recession-Ready</h3>Life throws curveballs, but SnackOrbit stands strong. Our vending machines are the unsung heroes of resilience. Rain or shine, they're there, serving up joy.</div>
  <div class="faint-brand brand">SnackOrbit</div>
</section>

<section class="cta-band">
  <div class="cta-photo" role="img" aria-label="Photo of a snack machine and a red drink machine side by side against a grey wall"></div>
  <div class="cta-copy">
    <h2>Ready to experience the SnackOrbit difference?</h2>
    <p>Sign up now and let's connect. Taste the future of snacking firsthand! Contact us today and explore how our vending magic can elevate your space.</p>
    <span class="solid">Contact Us</span>
  </div>
</section>

<section class="testi">
  <h2>Customer Testimonials</h2>
  <div class="arrow" style="left:90px"><svg width="16" height="10" viewBox="0 0 16 10"><path d="M15 5H2M5 1 1 5l4 4" stroke="#bbb" fill="none"/></svg></div>
  <div class="arrow" style="left:1073px"><svg width="16" height="10" viewBox="0 0 16 10"><path d="M1 5h13M11 1l4 4-4 4" stroke="#222" fill="none"/></svg></div>

  <div class="card" style="left:142px;top:185px">
    <p>Lorem ipsum dolor sit amet, amet ut ea consectetur adipiscing elit, sed do ex eiusmod tempor incididunt ut labore et dolore magna aliqua. Ut enim ad dolor minim veniam, quis nostrud amet ut ua exercitation.</p>
    <div class="card-foot"><div class="who">Owen Hale<span>Lorem Ipsum</span></div><div class="stars">★★★★★</div></div>
    <div class="avatar" role="img" aria-label="Customer portrait"></div>
  </div>
  <div class="card" style="left:466px;top:133px">
    <p>Lorem ipsum dolor sit amet, amet ut ea consectetur adipiscing elit, sed do ex eiusmod tempor incididunt ut labore et dolore magna aliqua. Ut enim ad dolor minim veniam, quis nostrud amet ut ua exercitation.</p>
    <div class="card-foot"><div class="who">Mara Lind<span>Lorem Ipsum</span></div><div class="stars">★★★★★</div></div>
    <div class="avatar" role="img" aria-label="Customer portrait"></div>
  </div>
  <div class="card" style="left:776px;top:185px">
    <p>Lorem ipsum dolor sit amet, amet ut ea consectetur adipiscing elit, sed do ex eiusmod tempor incididunt ut labore et dolore magna aliqua. Ut enim ad dolor minim veniam, quis nostrud amet ut ua exercitation.</p>
    <div class="card-foot"><div class="who">Theo Brandt<span>Lorem Ipsum</span></div><div class="stars">★★★★★</div></div>
    <div class="avatar" role="img" aria-label="Customer portrait"></div>
  </div>
</section>

<footer class="footer">
  <div class="brand">SnackOrbit</div>
  <div class="rule" style="top:169px"></div>
  <nav class="foot-links"><span class="on">Home</span><span>About</span><span>Why Choose Us</span><span>Products &amp; Services</span><span>Contact Us</span></nav>
  <div class="rule" style="top:226px"></div>
  <div class="contact-row">
    <div class="c-item"><div class="c-icon"><svg width="18" height="14" viewBox="0 0 18 14"><rect x="1" y="1" width="16" height="12" rx="1" stroke="#fff" fill="none" stroke-width="1.5"/><path d="M1 2l8 6 8-6" stroke="#fff" fill="none" stroke-width="1.5"/></svg></div><div><small>Email</small>info@snackorbit.com</div></div>
    <div class="c-item"><div class="c-icon"><svg width="14" height="18" viewBox="0 0 14 18"><path d="M7 17S1 10 1 7a6 6 0 0 1 12 0c0 3-6 10-6 10z" fill="#fff"/><circle cx="7" cy="7" r="2" fill="#3b3766"/></svg></div><div>123, Building Name,<br>Street City, State XY 1234</div></div>
    <div class="c-item"><div class="c-icon"><svg width="16" height="16" viewBox="0 0 16 16"><path d="M3 1l3 3-2 2q2 4 6 6l2-2 3 3-2 2Q6 15 1 3z" fill="#fff"/></svg></div><div><small>Phone</small><span style="font-size:15px">123-456-7890</span></div></div>
  </div>
</footer>
<div class="bottom"><span>© 2024 SnackOrbit. All Rights Reserved.</span><div class="socials"><i></i><i></i><i></i><i></i></div></div>

</body>
</html>
```